Field Basket - Store need a label design

We need a Label Design for our Cosmetic Line with Hemp Cosmetics. We do not want a hemp leaf on our design. We want our LOGO infront of the design with the name of the product (shower gel, body lotion, .....) The ingredients must be included as well as in the bottle within 12 months. The font is smaller than 3mm. Generally, the font must be at least 2mm in size. What we need: 100x140mm 200ml E 12m 4x as: Hemp - shampoo, shower gel, body lotion and hair balm 20x66 mm 50g E (2 pieces for front and back) as: face cream, hand cream 42x52mm as: lip balm (sample how it should look in the uploaded files with the name morvil) What else should be on it: WITHOUT artificial colors and fragrances WITHOUT paraffins WITHOUT silicones with pure hemp seed oil Product not tested on animals Manufacturer: MORVIL A-4812 GRUNDLACH Description: HANF-SHAMPOO 200 ml Skin-mild washing-active ingredients develop a particularly pleasant and gentle cleansing effect. High-quality hemp seed oil nourishes the hair in a natural way and makes it pleasantly soft, loose and supple. BRISK MEADOW- is suitable for all hair types, especially for damaged and dull hair. HEMP SHOWER BATH 200 ml The pleasant foam cleans mildly and gently. The excellent care effect of natural hemp seed oil makes skin and hair pleasantly soft and supple.BRISK MEADOW- is suitable for mild cleansing and care, especially of sensitive skin and damaged hair. HEMP-FOAM BATH 200 ml Skin-mild washing-active ingredients develop a particularly mild and creamy foam. The excellent care effect of natural hemp seed oil makes the skin exceptionally soft and supple.BRISK MEADOW- is suitable for mild cleansing and care, especially of sensitive, rough and chapped skin. HEMP HAIR BALM 200 ml A special combination of natural hemp seed oil and other high-quality vegetable oils cares for the hair perfectly and makes it pleasantly soft, loose, supple, naturally shiny, extremely easy to style and effectively prevents the cleavage of the tips. BRISK MEADOW HEMP HAIR BALM is suitable for all hair types, especially for damaged, damaged, brittle and dull hair, as well as split hair tips. HEMP BODY LOTION 200 ml Pure Hemp Seed Oil nourishes the skin naturally, prevents it from drying out too much and makes it particularly soft and supple.BRISK MEADOW HEMP BODY LOTION is for pleasant body care, especially after bathing, especially in dry, brittle and sensitive skin HEMP FACE CREAM 50 g The particularly high content of pure hemp seed oil nourishes the skin perfectly and makes it unusually soft and supple.BRISK MEADOW HEMP FACE CREAM is suitable for pleasant and moisturizing care of the entire face, especially for dry and brittle skin Skin. HEMP HAND CREAM 50 g The high content of pure hemp seed oil and natural beeswax protects and nourishes the skin perfectly and makes it soft and supple. BRISK MEADOW HEMP HAND CREAM is suitable for protective care especially of stressed, sensitive and brittle skin. HEMP LIP BALM 6 g Natural hemp seed oil, pure beeswax and other valuable ingredients provide long-lasting care for the lips and protect them from adverse weather conditions and dehydration.BRISK MEADOW HEMP LIP BALM is particularly suitable for the lasting care of sensitive, brittle and torn lips. HANF-SHAMPOO Ingredients (INCI): Aqua, Sodium Laureth Sulfate, TEA-Lauryl Sulfate, Disodium Laureth Sulfosuccinate, Potassium Cocoyl Hydrolized Collagen, Linoleamide-DEA, Cannabis Sativa Seed Oil, Natural Perfume, Sodium Chloride, Citric Acid, Potassium Sorbate, Panthenol , Tocopherol, chlorophyll, citral *, citronellol *, geraniol *, limonene *, linalool *. (* natural ingredients of essential oils). HEMP-DUSCHBAD Ingredients (INCI): Aqua, Sodium Laureth Sulfate, TEA-Lauryl Sulfate, Disodium Laureth Sulfosuccinate, Potassium Cocoyl Hydrolized Collagen, Cocoamphodiacetate, Linoleamide-DEA, Cocamidopropylamine Oxide, Cannabis Sativa Seed Oil, Natural Perfume, Coco-Glucoside, Glyceryl Oleate, Sodium Chloride, Citric Acid, Potassium Sorbate, Panthenol, Tocopherol, Chlorophyll, Citral *, Citronellol *, Geraniol *, Limonene *, Linalool *. (* natural ingredients of essential oils). HANF-SCHAUMBAD Ingredients (INCI): Aqua, MIPA-Pareth-25-Sulfate, Cocamidopropyl Betaine, Disodium Laureth Sulfosuccinate, Linoleamide-DEA, Cannabis Sativa Seed Oil, Coco-Glucoside, Glyceryl Oleate, Natural Perfume, Panthenol, Potassium Sorbate, Citric Acid, tocopherol, chlorophyll, citral *, citronellol *, geraniol *, limonene *, linalool *. * (* Natural constituents of essential oils). HANF-HAARBALSAM Ingredients (INCI): Aqua, Ceteareth-20, Cetearyl Alcohol, Dicocodimonium Chloride, Glycerine, Cannabis Sativa Seed Oil, Coco-Glucoside, Glyceryl Oleate, Natural Perfume, Potassium Sorbate, Panthenol, Citric Acid, Tocopherol, Chlorophyll, Citral *, Citronellol *, geraniol *, limonene *, linalool *. (* natural ingredients of essential oils). Hemp Facial Ingredients (INCI): Aqua, Cannabis Sativa Seed Oil, Cetearyl Alcohol, Cetearyl Glucoside, Sodium Cetearyl Sulfate, Hexyl Decanol, Glycerine, Natural Perfume, Benzyl Alcohol, Potassium Sorbate, Sodium Benzoate, Tocopherol, Panthenol, Citric Acid, Citral * , Citronellol *, geraniol *, limonene *, linalool *. (* natural ingredients of essential oils). HANF HAND CREAM Ingredients (INCI): Cannabis sativa Seed Oil, Cocos Nucifera Oil, Cera Alba, Tocopherol, Natural Perfume, Citral *, Citronellol *, Geraniol *, Limonene *, Linalool *. (* natural ingredients of essential oils). HEMP BODY LOTION INGREDIENTS (INCI): Aqua, Cannabis Sativa Seed Oil, Cetearyl Alcohol, Ceteareth-12, Cetearyl Glucoside, Glycerol, Hexyldecanol, Natural Perfume, Benzyl Alcohol, Potassium Sorbate, Sodium Benzoate, Tocopherol, Panthenol, Citric Acid, Geraniol , Limonene *, linalool *, citronellol *, citral *, (* natural constituents of essential oils). HEMP LIP BALM Ingredients (INCI): Cannabis sativa Seed Oil, Cocos nucifera Oil, Cera Alba, Natural Perfume, Citral *, Citronellol *, Geraniol *, Limonene *, Linalool *. (* natural ingredients of essential oils).

Colors

Designer to choose colors to be used in the design.

Requirements
Must have
• The Sentence: Natural Spirit - Feel the nature should be in front of the label as our slogan for the Cosmetic Line
Should not have
• Hemp leaf

```html
<!DOCTYPE html>
<html lang="de">
<head>
<meta charset="utf-8">
<title>Hanf Gesichtscreme – Etikett Rückseite</title>
<link rel="stylesheet" href="https://fonts.googleapis.com/css2?family=Roboto:wght@400;700&family=Kalam:wght@400;700&display=swap">
<style>
  :root {
    --label-red: #c8575b;
    --ink-white: #ffffff;
  }
  html, body {
    margin: 0;
    padding: 0;
    overflow: hidden;
    background: var(--ink-white);
  }
  .label {
    position: relative;
    width: 1200px;
    height: 366px;
    background: var(--label-red);
    color: var(--ink-white);
    overflow: hidden;
  }
  .description {
    position: absolute;
    left: 14px;
    top: 10px;
    width: 680px;
    margin: 0;
    font-family: "Roboto", Arial, sans-serif;
    font-size: 25.5px;
    line-height: 42px;
  }
  .usage {
    position: absolute;
    left: 14px;
    top: 170px;
    width: 680px;
    margin: 0;
    font-family: "Kalam", cursive;
    font-size: 29px;
    line-height: 45px;
    transform: skewX(-6deg);
  }
  .usage .line-name {
    font-family: "Courier New", monospace;
    font-weight: 700;
    letter-spacing: 1px;
  }
  .divider-main {
    position: absolute;
    left: 706px;
    top: 0;
    width: 2px;
    height: 366px;
    background: var(--ink-white);
  }
  .ingredients {
    position: absolute;
    left: 732px;
    top: 10px;
    width: 456px;
    margin: 0;
    font-family: "Roboto", Arial, sans-serif;
    font-size: 20px;
    line-height: 29.5px;
    text-align: justify;
  }
  .rule-bottom {
    position: absolute;
    left: 706px;
    top: 270px;
    width: 494px;
    height: 2px;
    background: var(--ink-white);
  }
  .info-row {
    position: absolute;
    left: 708px;
    top: 272px;
    width: 492px;
    height: 94px;
    display: flex;
    align-items: center;
  }
  .info-cell {
    height: 100%;
    display: flex;
    align-items: center;
    justify-content: center;
    border-right: 2px solid var(--ink-white);
  }
  .info-cell:last-child { border-right: none; }
  .net-content {
    width: 150px;
    font-family: "Roboto", Arial, sans-serif;
    font-weight: 700;
    font-size: 32px;
  }
  .estimated-sign {
    width: 152px;
    font-family: "Roboto", Arial, sans-serif;
    font-size: 36px;
  }
  .disposal { flex: 1; }
</style>
</head>
<body>
<div class="label">
  <p class="description">Der besonders hohe Gehalt an reinem Hanfsamen-Öl pflegt die Haut hervorragend und macht sie ungewöhnlich weich und geschmeidig.</p>

  <p class="usage"><span class="line-name">BRISK MEADOW</span> – eignet sich zur angenehmen und feuchtigkeitsspendenden Pflege der gesamten Gesichtspartie besonders bei trockener und spröder Haut.</p>

  <div class="divider-main"></div>

  <p class="ingredients">Ingredients (INCI): Aqua, Cannabis sativa Seed Oil, Cetearyl Alcohol, Cetearyl Glucoside, Sodium Cetearyl Sulfate, Hexyldecanol, Glycerine, Natural Perfume, Benzyl Alcohol, Potassium Sorbate, Sodium Benzoate, Tocopherol, Panthenol, Citric Acid, Citral*, Citronellol*, Geraniol*, Limonene*, Linalool*. (* natürliche Bestandteile ätherischer Öle).</p>

  <div class="rule-bottom"></div>

  <div class="info-row">
    <div class="info-cell net-content">50 mg</div>
    <div class="info-cell estimated-sign">e</div>
    <div class="info-cell disposal">
      <svg width="40" height="46" viewBox="0 0 40 46" role="img" aria-label="Entsorgungssymbol Mülltonne">
        <g fill="none" stroke="#ffffff" stroke-width="2.5" stroke-linecap="round">
          <line x1="8" y1="12" x2="32" y2="12"/>
          <path d="M15 12 V8 H25 V12"/>
          <path d="M11 12 L13 38 H27 L29 12"/>
          <line x1="4" y1="4" x2="36" y2="42"/>
        </g>
        <rect x="10" y="41" width="20" height="4" fill="#ffffff"/>
      </svg>
    </div>
  </div>
</div>
</body>
</html>
```